PowerPoint Listing Presentation for Real Estate Agency

We need a PowerPoint presentation for a new real estate brokerage team.

[[[[[[submit 1-3 sample slides for review - i will provide feedback and you can make changes if you want to - we will not be deciding on a design prior to the deadline]]]]]

******ATTN: DESIGNERS, if your skills are webdesign then just look at this like a portable website or a brochure. it should be easy enough******

NOTE: we have all the data to put into the slides. You just need to come up with the design and layout. we have a sample design that we like and have provided.

This focus will be for the home listing side of the business (a presentation for home sellers to convince them to use our services). The data and slides will present our team and the benefits, in the best light, to use our services over that of other real estate agent applying for the job. This presentation will proved facts and benefits and describe our special and unique offerings that will show a home seller why we can sell their home for more money in less time and with the least amount of hassle. The main color scheme is Dark Blue and White (we want some additional colors included - based on your creativity. otherwise the presentation will too monotone). We would like to see the use of Statistical Graphs (3-D) - data provided. We have photos of our team and a new logo (the logo could have some minor adjustment to clean it up if necessary) - also uploaded. We have about 80-90% of the information that will be put into the slides and will need to work closely to get the design and data integrated into the presentation (should be easier then it sounds). We should be able to add slides and data 'at will' over time via our master slides built into the presentation. We have a pretty good sample presentation that we like and can be used as a guideline (this is from our affiliated business network and we have full rights to all the information), it is uploaded but doesn't contain all the slide because of size limitations.

NOTE: An additional buyers presentation will be needed after we get the sellers presentation completed, which means additional work.

This should be enough to get you started and we are available if you have any questions to help you with the project. there will be around 60-70 total slides. once concept is completed it will be easy to create the slides.

Target Market(s)

home sellers. people who are moving to a new and better home or relocation for job reasons. typically more established in life

Industry/Entity Type

Real Estate

Requirements
Must have
• all the slides must be congruent. in other words, the exact same layout feel should used across the board. we are working on building our trade dress/image. Also, it must have a soft and inviting overall feel, yet show strength of ability.
Nice to have
• nice to have use of real people images when necessary. 3D graphs would be nice. clean modern look and feel, yet sophisticated and professional.
Should not have
• should not have a lot of time consuming transitions. do not include 3D stick figures or distracting moving gifs

```html
<!DOCTYPE html>
<html lang="en">
<head>
<meta charset="utf-8">
<title>Top 20 Reasons People Do Not Go Back to Their Agent</title>
<link rel="stylesheet" href="https://fonts.googleapis.com/css2?family=Tinos:wght@400;700&display=swap">
<style>
  :root {
    --navy: #0f2a5c;
    --navy-deep: #0a1f47;
    --gold: #f2b01e;
    --ink: #16264a;
    --accent: #2f6fd6;
    --tick: #2a78e4;
    --paper: #ffffff;
    --paper-tint: #dfe8f3;
  }
  * { margin: 0; padding: 0; box-sizing: border-box; }
  html, body { width: 1200px; height: 900px; overflow: hidden; background: var(--paper); }
  .slide {
    position: relative;
    width: 1200px;
    height: 900px;
    overflow: hidden;
    font-family: "Tinos", "Times New Roman", serif;
    color: var(--ink);
    background: linear-gradient(180deg, var(--paper) 0%, #f2f6fb 45%, var(--paper-tint) 100%);
  }
  .frame { position: absolute; inset: 0; }
  .backdrop-house {
    position: absolute;
    left: 150px; top: 230px;
    width: 880px; height: 640px;
    background: radial-gradient(ellipse at center, rgba(150,175,210,0.16) 0%, rgba(150,175,210,0) 70%);
  }
  .title {
    position: absolute;
    left: 428px; top: 64px;
    font-size: 30px;
    font-weight: 400;
    color: var(--navy-deep);
    white-space: nowrap;
  }
  .title em { font-style: normal; color: var(--accent); }
  .title-icon { position: absolute; left: 340px; top: 50px; }
  .reasons { list-style: none; position: absolute; }
  .reasons li {
    position: absolute;
    left: 0;
    width: 480px;
    padding-left: 30px;
    font-size: 23.5px;
    line-height: 32px;
    white-space: nowrap;
  }
  .reasons li svg { position: absolute; left: 0; top: 7px; }
  .reasons--left { left: 98px; top: 0; }
  .reasons--right { left: 623px; top: 0; }
  .house-cluster {
    position: absolute;
    left: 22px; top: 800px;
    width: 180px; height: 82px;
    background: linear-gradient(180deg, #1f4f9a, var(--navy));
    border-radius: 4px;
  }
  .brand-tile {
    position: absolute;
    left: 1054px; top: 762px;
    width: 120px; height: 120px;
    background: var(--paper);
    display: flex; align-items: center; justify-content: center;
    text-align: center;
  }
  .brand-name {
    font-size: 17px;
    font-weight: 700;
    color: var(--navy);
    line-height: 20px;
    letter-spacing: 0.5px;
  }
</style>
</head>
<body>
<div class="slide">
  <svg class="frame" width="1200" height="900" viewBox="0 0 1200 900" aria-hidden="true">
    <defs>
      <linearGradient id="bandNavy" x1="0" y1="0" x2="1" y2="1">
        <stop offset="0" stop-color="#17397a"/>
        <stop offset="1" stop-color="#0a1f47"/>
      </linearGradient>
      <symbol id="tick" viewBox="0 0 20 20">
        <rect x="1" y="4" width="14" height="14" fill="none" stroke="#2a78e4" stroke-width="1.6"/>
        <path d="M4 10 L8 14 L18 2" fill="none" stroke="#2a78e4" stroke-width="3" stroke-linecap="round" stroke-linejoin="round"/>
      </symbol>
    </defs>
    <!-- left band -->
    <path d="M0 0 L350 0 Q70 170 0 590 Z" fill="url(#bandNavy)"/>
    <path d="M350 0 Q70 170 0 590" fill="none" stroke="#ffffff" stroke-width="6" opacity="0.7"/>
    <!-- top-right band -->
    <path d="M330 0 L1200 0 L1200 40 Q800 6 330 0 Z" fill="url(#bandNavy)"/>
    <path d="M300 0 Q820 10 1200 48" fill="none" stroke="var(--gold)" stroke-width="5"/>
    <!-- bottom-right band -->
    <path d="M560 900 Q1060 690 1200 200 L1200 900 Z" fill="url(#bandNavy)"/>
    <path d="M560 900 Q1060 690 1200 200" fill="none" stroke="var(--gold)" stroke-width="7"/>
    <path d="M520 900 Q1030 700 1200 150" fill="none" stroke="#ffffff" stroke-width="3" opacity="0.8"/>
  </svg>

  <div class="backdrop-house" role="img" aria-label="Faint outline of a house in the background"></div>

  <svg class="title-icon" width="66" height="66" viewBox="0 0 66 66" role="img" aria-label="Home icon">
    <circle cx="33" cy="33" r="31" fill="var(--navy)" stroke="#c9d6ea" stroke-width="3"/>
    <path d="M17 33 L33 19 L49 33" fill="none" stroke="#ffffff" stroke-width="3.5" stroke-linejoin="round" stroke-linecap="round"/>
    <path d="M22 31 V47 H44 V31" fill="none" stroke="#ffffff" stroke-width="3"/>
    <rect x="29" y="36" width="8" height="11" fill="#ffffff"/>
  </svg>
  <h1 class="title">Top <em>20 Reasons</em> People Do Not Go Back to Their Agent</h1>

  <ul class="reasons reasons--left">
    <li style="top:213px"><svg width="20" height="20"><use href="#tick"/></svg>Poor Communication</li>
    <li style="top:260px"><svg width="20" height="20"><use href="#tick"/></svg>Over-Promised, Under-Delivered</li>
    <li style="top:306px"><svg width="20" height="20"><use href="#tick"/></svg>Promised a Selling Price Far from Reality</li>
    <li style="top:351px"><svg width="20" height="20"><use href="#tick"/></svg>Promised Speed-of-Sale Far from Reality</li>
    <li style="top:396px"><svg width="20" height="20"><use href="#tick"/></svg>Were Less Experienced than They<br>Presented Themselves</li>
    <li style="top:474px"><svg width="20" height="20"><use href="#tick"/></svg>Wasted a Lot of Time Showing Home to<br>Unqualified Buyers</li>
    <li style="top:553px"><svg width="20" height="20"><use href="#tick"/></svg>Left Out a Contract Detail</li>
    <li style="top:599px"><svg width="20" height="20"><use href="#tick"/></svg>Lack of Professionalism</li>
    <li style="top:642px"><svg width="20" height="20"><use href="#tick"/></svg>Hard to get a Hold of</li>
    <li style="top:690px"><svg width="20" height="20"><use href="#tick"/></svg>Didn’t Market the Home Properly</li>
    <li style="top:735px"><svg width="20" height="20"><use href="#tick"/></svg>Never Showed the Home</li>
  </ul>

  <ul class="reasons reasons--right">
    <li style="top:214px"><svg width="20" height="20"><use href="#tick"/></svg>Too Pushy</li>
    <li style="top:264px"><svg width="20" height="20"><use href="#tick"/></svg>Didn’t Help Stage the Home for Sale</li>
    <li style="top:314px"><svg width="20" height="20"><use href="#tick"/></svg>Lack of Representation</li>
    <li style="top:364px"><svg width="20" height="20"><use href="#tick"/></svg>Poor Negotiating Skills</li>
    <li style="top:414px"><svg width="20" height="20"><use href="#tick"/></svg>Sold the Home for a Low Price</li>
    <li style="top:465px"><svg width="20" height="20"><use href="#tick"/></svg>Too Busy</li>
    <li style="top:513px"><svg width="20" height="20"><use href="#tick"/></svg>Home Didn’t Sell</li>
    <li style="top:561px"><svg width="20" height="20"><use href="#tick"/></svg>Didn’t do Anything Seller<br>Couldn’t Have Done Themselves</li>
    <li style="top:640px"><svg width="20" height="20"><use href="#tick"/></svg>Didn’t Keep In<br>Touch/No Feedback</li>
  </ul>

  <div class="house-cluster" role="img" aria-label="Illustration of three small houses in a row"></div>

  <div class="brand-tile">
    <span class="brand-name">HARLOW<br>&amp; REED</span>
  </div>
</div>
</body>
</html>
```